Harbor Ledger Funds Bus card and Logo

I need a logo design and Bus card design. The fund focuses on evaluating and investing in minerals (sub-surface rights) and real estate.

Harbor ledger refers to a book of knowledge that each plebe gets when entering the Kelmont Marine Academy (my alma mater)

Target Market(s)

Investors and financial advisors

Contact Information for Business Card

Simple - perhaps a logo with a theme on book of knowledge

Logo Text

Ex Scientia Imperium

Font styles to use
Serif
Sans Serif

Colors

Designer to choose colors to be used in the design.

Requirements
Must have
• memorable logo that is relatively simple

```html
<!DOCTYPE html>
<html lang="en">
<head>
<meta charset="utf-8">
<title>Harbor Ledger Funds – Business Card</title>
<link rel="stylesheet" href="https://fonts.googleapis.com/css2?family=Roboto:wght@400;700&display=swap">
<style>
  :root {
    --page-bg: #ecebe8;
    --card-green: #86c73d;
    --card-blue: #3399cf;
    --disc-white: #f4f4f4;
    --text-light: #ffffff;
    --text-dark: #2a2a2a;
    --rule-grey: #8a8a8a;
  }
  * { margin: 0; padding: 0; box-sizing: border-box; }
  html, body {
    width: 1200px; height: 900px; overflow: hidden;
    background: var(--page-bg);
    font-family: "Roboto", Arial, sans-serif;
  }
  .business-card {
    position: absolute;
    left: 120px; top: 153px;
    width: 960px; height: 593px;
    background: var(--card-blue);
    overflow: hidden;
    box-shadow: 0 12px 30px rgba(0,0,0,0.18);
  }
  .green-panel {
    position: absolute; left: 0; top: 0;
    width: 680px; height: 100%;
    background: var(--card-green);
  }
  .brand-disc {
    position: absolute;
    left: 422px; top: 35px;
    width: 516px; height: 516px;
    border-radius: 50%;
    background: var(--disc-white);
    display: flex; flex-direction: column;
    align-items: center; justify-content: center;
    padding-top: 150px;
  }
  .brand-name {
    color: var(--text-dark);
    font-weight: 700;
    font-size: 42px;
    letter-spacing: 0.5px;
    text-transform: uppercase;
    text-align: center;
    line-height: 1.1;
  }
  .brand-rule {
    width: 370px; height: 2px;
    background: var(--rule-grey);
    margin-top: 14px;
  }
  .holder { position: absolute; left: 54px; top: 62px; color: var(--text-light); }
  .holder-name { font-weight: 700; font-size: 35px; text-transform: uppercase; letter-spacing: 0.3px; }
  .holder-title { font-size: 26px; margin-top: 2px; }
  .contact-list {
    position: absolute; left: 54px; top: 292px;
    list-style: none; color: var(--text-light); font-size: 26px;
  }
  .contact-list li { display: flex; align-items: center; height: 35px; }
  .contact-list svg { width: 22px; height: 22px; margin-right: 8px; fill: var(--text-light); flex: none; }
  .address { position: absolute; left: 54px; top: 455px; color: var(--text-light); font-size: 26px; line-height: 34px; }
</style>
</head>
<body>
  <section class="business-card">
    <div class="green-panel"></div>

    <div class="holder">
      <p class="holder-name">Marcus Delaney</p>
      <p class="holder-title">Managing Director</p>
    </div>

    <ul class="contact-list">
      <li><svg viewBox="0 0 24 24" aria-hidden="true"><path d="M2 9c0-3 4-5 10-5s10 2 10 5v2h-5V9c-2-.7-8-.7-10 0v2H2z"/><path d="M6 12h12l2 8H4z"/></svg>044-555 010 200</li>
      <li><svg viewBox="0 0 24 24" aria-hidden="true"><path d="M7 1h10a1 1 0 0 1 1 1v20a1 1 0 0 1-1 1H7a1 1 0 0 1-1-1V2a1 1 0 0 1 1-1zm1 3v14h8V4zm4 15.5a1.2 1.2 0 1 0 0 2.4 1.2 1.2 0 0 0 0-2.4z"/></svg>044-555 010 200</li>
      <li><svg viewBox="0 0 24 24" aria-hidden="true"><path d="M2 5h20v14H2z M3.5 6.5l8.5 6.5 8.5-6.5" stroke="#86c73d" stroke-width="1.5"/></svg>info@harborledgerfunds.com</li>
      <li><svg viewBox="0 0 24 24" aria-hidden="true"><circle cx="12" cy="12" r="10"/><path d="M8 6c2 1 1 3 3 4s0 3 2 4-1 4 0 6M15 4c-1 2 2 3 4 4" stroke="#86c73d" stroke-width="1.6" fill="none"/></svg>www.harborledgerfunds.com</li>
    </ul>

    <p class="address">12345, Address Goes Here<br>Country Name, 123456</p>

    <div class="brand-disc">
      <p class="brand-name">Harbor Ledger<br>Funds</p>
      <div class="brand-rule"></div>
    </div>
  </section>
</body>
</html>
```